BRIGHT RIVER POWER.

I'd like my business logo.
contact name: Dennis Halvorsen
phone:0438759164
email: info@brightriverpower.net.au
website: www.brightriverpower.net.au

services:
solar
battery storage
LED lighting
energy saving solutions
general electrical
I'd like the design to look professional

Target Market(s)

Everyone

Industry/Entity Type

Business

Contact Information for Business Card

as described above

Requirements
Must have
• Id like the colours and the design to work well with my logo.

```html
<!DOCTYPE html>
<html lang="en">
<head>
<meta charset="utf-8">
<title>Bright River Power – Business Card</title>
<link rel="stylesheet" href="https://fonts.googleapis.com/css2?family=Montserrat:wght@400;500;600&display=swap">
<style>
  :root {
    --bg: #ece9e4;
    --card: #ffffff;
    --green: #2e9e46;
    --green-text: #3aa34f;
    --orange: #e3861f;
  }
  html, body {
    margin: 0;
    padding: 0;
    width: 1200px;
    height: 1022px;
    overflow: hidden;
    background: var(--bg);
    font-family: "Montserrat", Arial, sans-serif;
  }
  .stage { position: relative; width: 1200px; height: 1022px; }
  .card {
    position: absolute;
    left: 120px;
    top: 211px;
    width: 960px;
    height: 600px;
    background: var(--card);
    border-radius: 22px;
    overflow: hidden;
    box-shadow: 0 18px 40px rgba(0,0,0,0.18);
  }
  .edge-band {
    position: absolute;
    bottom: 0;
    height: 36px;
  }
  .edge-band--left { left: 0; width: 52%; background: var(--orange); }
  .edge-band--right { right: 0; width: 48%; background: var(--green); }
  .side-dot {
    position: absolute;
    left: -40px;
    top: 320px;
    width: 80px;
    height: 80px;
    border-radius: 50%;
    background: var(--green);
  }
  .brand {
    position: absolute;
    left: 320px;
    top: 120px;
    display: flex;
    align-items: center;
    gap: 18px;
  }
  .brand__mark {
    width: 56px;
    height: 56px;
    border-radius: 50%;
    background: var(--orange);
    flex: none;
  }
  .brand__name {
    font-weight: 600;
    font-size: 40px;
    letter-spacing: 1px;
    color: var(--green);
    white-space: nowrap;
  }
  .divider {
    position: absolute;
    left: 90px;
    right: 60px;
    top: 360px;
    height: 2px;
    background: var(--green);
  }
  .contact__name {
    position: absolute;
    left: 90px;
    top: 306px;
    margin: 0;
    font-weight: 500;
    font-size: 34px;
    line-height: 40px;
    color: var(--orange);
  }
  .contact__list {
    position: absolute;
    left: 110px;
    top: 384px;
    margin: 0;
    padding: 0;
    list-style: none;
  }
  .contact__list li {
    display: flex;
    align-items: center;
    gap: 14px;
    font-size: 22px;
    line-height: 40px;
    color: var(--green-text);
  }
  .contact__list svg { width: 16px; height: 16px; flex: none; }
  .services {
    position: absolute;
    right: 50px;
    top: 378px;
    margin: 0;
    padding: 0;
    list-style: none;
    text-align: right;
  }
  .services li {
    position: relative;
    font-size: 22px;
    line-height: 34px;
    color: var(--green-text);
    padding-right: 30px;
    white-space: nowrap;
  }
  .services li::after {
    content: "";
    position: absolute;
    right: 0;
    top: 12px;
    width: 10px;
    height: 10px;
    border-radius: 50%;
    background: var(--orange);
  }
</style>
</head>
<body>
<div class="stage">
  <div class="card">
    <div class="edge-band edge-band--left"></div>
    <div class="edge-band edge-band--right"></div>
    <div class="side-dot"></div>

    <div class="brand">
      <div class="brand__mark"></div>
      <div class="brand__name">BRIGHT RIVER POWER</div>
    </div>

    <p class="contact__name">Dennis Halvorsen</p>
    <div class="divider"></div>

    <ul class="contact__list">
      <li>
        <svg viewBox="0 0 16 16" aria-hidden="true"><path d="M4 1.5 6.2 4 5 5.6c.8 2 2.4 3.6 4.4 4.4L11 8.8l2.5 2.2-1.4 2.6C7 13.4 2.6 9 2.4 3.9Z" fill="var(--orange)"/></svg>
        0438759164
      </li>
      <li>
        <svg viewBox="0 0 16 16" aria-hidden="true"><rect x="1.5" y="3.5" width="13" height="9" rx="1" fill="none" stroke="var(--orange)" stroke-width="1.6"/><path d="M2 4.5 8 9l6-4.5" fill="none" stroke="var(--orange)" stroke-width="1.6"/></svg>
        info@brightriverpower.net.au
      </li>
      <li>
        <svg viewBox="0 0 16 16" aria-hidden="true"><circle cx="8" cy="8" r="6.5" fill="none" stroke="var(--orange)" stroke-width="1.5"/><ellipse cx="8" cy="8" rx="2.8" ry="6.5" fill="none" stroke="var(--orange)" stroke-width="1.2"/><path d="M1.5 8h13" stroke="var(--orange)" stroke-width="1.2"/></svg>
        www.brightriverpower.net.au
      </li>
    </ul>

    <ul class="services">
      <li>Solar</li>
      <li>Battery storage</li>
      <li>LED lighting</li>
      <li>Energy saving solutions</li>
      <li>General electrical</li>
    </ul>
  </div>
</div>
</body>
</html>
```